Falkrin homes and renovations business card design.

Would like some new card designs utilizing my new logo that look professional. I am open to different colors on the logo or utilize the same ones we have. I like the original concept but would like to see some fresh ideas and build on what we have already done.

Target Market(s)

Custom home building industry, Real estate sales, Renovation projects.

Industry/Entity Type

Home Builder

Contact Information for Business Card

Falkrin Homes and Renovations
2871 96th Avenue
Carrowby, Westvale
T2R3W8
Home : 403- 718-4063 Cell: 403- 294-5170

My info is : Dax Falkrin, President and CEO
email: falkrinhomes@maildrop-example.net
Website: falkrinhomes-example.com
websit

Requirements
Must have
• Must Use my new logo design. I am open to different colors on the logo or utilize the same ones in the existing design. I can upload the original logo design if needed.

```html
<!DOCTYPE html>
<html lang="en">
<head>
<meta charset="utf-8">
<title>Falkrin Homes and Renovations – Business Card</title>
<link href="https://fonts.googleapis.com/css2?family=Open+Sans:wght@400;600;700&display=swap" rel="stylesheet">
<style>
  :root {
    --gold: #b08a3e;
    --ink: #1f1f1f;
    --card-black: #050505;
    --card-white: #ffffff;
    --backdrop: #e9e6e1;
  }
  * { box-sizing: border-box; margin: 0; padding: 0; }
  html, body { width: 1200px; height: 900px; overflow: hidden; }
  body {
    background: var(--backdrop);
    font-family: "Open Sans", Arial, sans-serif;
    display: flex;
    flex-direction: column;
    align-items: center;
    justify-content: center;
    gap: 60px;
  }
  .card {
    width: 640px;
    height: 366px;
    position: relative;
    box-shadow: 0 6px 18px rgba(0,0,0,0.18);
  }
  .card--back {
    background: var(--card-black);
    display: flex;
    align-items: center;
    justify-content: center;
  }
  .brand {
    color: var(--gold);
    font-weight: 600;
    text-transform: uppercase;
    line-height: 1;
  }
  .brand__name { display: block; letter-spacing: 1px; }
  .brand__sub { display: block; letter-spacing: 1px; }
  .card--back .brand { display: flex; align-items: center; gap: 18px; }
  .card--back .brand__mark { width: 22px; height: 22px; background: var(--gold); }
  .card--back .brand__name { font-size: 64px; }
  .card--back .brand__sub { font-size: 21px; margin-top: 4px; }

  .card--front { background: var(--card-white); overflow: hidden; }
  .card--front .brand { position: absolute; left: 44px; top: 42px; }
  .card--front .brand__name { font-size: 60px; }
  .card--front .brand__sub { font-size: 20px; margin-top: 2px; }
  .person { position: absolute; left: 54px; top: 196px; }
  .person__name { color: var(--gold); font-weight: 700; font-size: 23px; letter-spacing: 0.5px; }
  .person__title { color: var(--ink); font-size: 15px; margin: 2px 0 0 8px; }
  .contacts { list-style: none; margin: 14px 0 0 16px; }
  .contacts li {
    display: flex; align-items: center; gap: 10px;
    font-size: 15px; color: var(--ink); line-height: 22px;
  }
  .contacts svg { width: 13px; height: 13px; fill: var(--gold); flex: none; }
  .office {
    position: absolute; right: 36px; top: 176px;
    text-align: right; font-size: 13px; color: var(--ink); line-height: 19px;
    font-style: normal;
  }
  .office__name { color: var(--gold); font-weight: 600; text-transform: uppercase; }
</style>
</head>
<body>
  <section class="card card--back">
    <div class="brand">
      <span class="brand__mark"></span>
      <span>
        <span class="brand__name">Falkrin</span>
        <span class="brand__sub">Homes and Renovations</span>
      </span>
    </div>
  </section>

  <section class="card card--front">
    <div class="brand">
      <span class="brand__name">Falkrin</span>
      <span class="brand__sub">Homes and Renovations</span>
    </div>

    <div class="person">
      <p class="person__name">DAX FALKRIN</p>
      <p class="person__title">President and CEO</p>
      <ul class="contacts">
        <li><svg viewBox="0 0 16 16"><path d="M3 1l3 3-1.5 2a9 9 0 005.5 5.5L12 10l3 3-2 2C7 15 1 9 1 3z"/></svg>403- 718-4063</li>
        <li><svg viewBox="0 0 16 16"><path d="M4 0h8a1 1 0 011 1v14a1 1 0 01-1 1H4a1 1 0 01-1-1V1a1 1 0 011-1zm1 2v10h6V2zm3 11a1 1 0 100 2 1 1 0 000-2z"/></svg>403- 294-5170</li>
        <li><svg viewBox="0 0 16 16"><path d="M0 3h16v1L8 9 0 4zm0 3l8 5 8-5v7H0z"/></svg>falkrinhomes@maildrop-example.net</li>
        <li><svg viewBox="0 0 16 16"><circle cx="8" cy="8" r="8"/></svg>www.falkrinhomes-example.com</li>
      </ul>
    </div>

    <address class="office">
      <p class="office__name">Falkrin Homes and<br>Renovations</p>
      <p>2871 96th Avenue</p>
      <p>Carrowby, Westvale T2R3W8</p>
    </address>
  </section>
</body>
</html>
```